Lawn care business card

I am looking for a quality designed personal business card to represent the quality and elegant nature of our company. We separate ourselves in our market by the aesthetic value of our work, so I am looking for marketing material that does the same. We target our marketing high end customers, and we try to avoid price shoppers. I am open to all design options, so long as they are in line with our companies values.

We are tend to go with a retro look on everything from our logo and print material, to our uniforms. We like to portray and "old fashion" set of core values, with a modern elegance. So a wild and crazy look is out of the question.

Things I'd like on the card:
1.) Logo
2.) Phone number: (816) 555-2931
3.) Website: Verdelynkc.com
4.) Email: robertfairley@verdelynkc.com
5.) My name: Robert Fairley
6.) Facebook link: facebook.com/VerdelynGardenandGrounds
7.) Instagram: http://instagram.com/verdelynkc

Attached is a copy of our logo.

Reason: More time is needed to gather conclusive feedback from the members of our marketing team.

```html
<!DOCTYPE html>
<html lang="en">
<head>
<meta charset="utf-8">
<title>Verdelyn Business Card</title>
<link rel="stylesheet" href="https://fonts.googleapis.com/css2?family=Arimo:wght@400;700&display=swap">
<style>
  :root {
    --backdrop: #7c8893;
    --card: #1e2021;
    --ink: #f2f2f2;
    --accent: #e2622a;
  }
  * { margin: 0; padding: 0; box-sizing: border-box; }
  html, body {
    width: 1200px;
    height: 1000px;
    overflow: hidden;
    background: var(--backdrop);
  }
  .card {
    position: absolute;
    left: 100px;
    top: 214px;
    width: 1000px;
    height: 572px;
    background: var(--card);
    border-radius: 4px;
    font-family: "Arimo", Arial, sans-serif;
    color: var(--ink);
  }
  .brand {
    position: absolute;
    right: 90px;
    top: 110px;
    display: flex;
    align-items: center;
    gap: 18px;
  }
  .brand-dot {
    width: 34px;
    height: 34px;
    border-radius: 50%;
    background: var(--accent);
  }
  .brand-name {
    font-size: 52px;
    font-weight: 700;
    letter-spacing: 2px;
    text-transform: uppercase;
    color: var(--ink);
  }
  .holder-name {
    position: absolute;
    left: 80px;
    top: 232px;
    font-size: 30px;
    font-weight: 700;
  }
  .contact-list {
    position: absolute;
    left: 80px;
    top: 372px;
    list-style: none;
    font-size: 22px;
    font-weight: 700;
    line-height: 34px;
  }
</style>
</head>
<body>
  <main class="card">
    <div class="brand">
      <span class="brand-dot"></span>
      <span class="brand-name">Verdelyn</span>
    </div>
    <h1 class="holder-name">Robert Fairley</h1>
    <ul class="contact-list">
      <li>Phone : (816) 555-2931</li>
      <li>Email : robertfairley@verdelynkc.com</li>
      <li>Website : Verdelynkc.com</li>
      <li>Instagram : http://instagram.com/verdelynkc</li>
      <li>Facebook : facebook.com/VerdelynGardenandGrounds</li>
    </ul>
  </main>
</body>
</html>
```